Design logo and business card.

Design and construct logo and card for my business which is an over seeing company of other smaller businesses. The companies name is ember4 business works. Im open to any ideas but i am looking for a very cool contemporary design with a very prestige feel. The card can be either single or double sided, Thank you and i will look forward to your submissions.

Business

• Company name, email, website, telephone, my name. Cool modern look with a prestige feel.

```html
<!DOCTYPE html>
<html lang="en">
<head>
<meta charset="utf-8">
<title>ember4 business works — business card</title>
<link rel="stylesheet" href="https://fonts.googleapis.com/css2?family=Raleway:wght@200;300&display=swap">
<style>
  :root {
    --stage: #3c3c3e;
    --card-base: #0d0d0f;
    --card-tone: #1b1b1f;
    --ink: #f2f2f4;
    --ink-soft: #c9c9cf;
    --accent: #2aa3d8;
    --accent-glow: rgba(60, 170, 230, 0.55);
  }
  * { margin: 0; padding: 0; box-sizing: border-box; }
  html, body {
    width: 1200px; height: 887px; overflow: hidden;
    background: var(--stage);
    font-family: "Raleway", "Helvetica Neue", Arial, sans-serif;
  }
  .canvas { position: relative; width: 1200px; height: 887px; }

  .card {
    position: absolute;
    width: 580px; height: 350px;
    background: var(--card-base);
    overflow: hidden;
    box-shadow: 0 14px 30px rgba(0,0,0,0.45);
  }
  .card--front { left: 70px; top: 90px; }
  .card--back  { left: 560px; top: 440px; }

  .card__pattern {
    position: absolute; inset: 0;
    background: radial-gradient(ellipse at 50% 45%, var(--card-tone) 0%, var(--card-base) 75%);
  }

  .wordmark {
    position: absolute;
    display: flex; align-items: center; gap: 16px;
    color: var(--ink); font-weight: 300;
  }
  .wordmark__dot {
    width: 18px; height: 18px; border-radius: 50%;
    background: var(--accent);
    box-shadow: 0 0 12px var(--accent-glow);
  }
  .wordmark__text { line-height: 1.05; letter-spacing: 0.02em; }

  .card--front .wordmark { left: 150px; top: 118px; }
  .card--front .wordmark__text { font-size: 48px; }
  .card--front .wordmark__text small { display: block; font-size: 24px; letter-spacing: 0.04em; }

  .card--back .wordmark { left: 96px; top: 140px; gap: 10px; }
  .card--back .wordmark__dot { width: 10px; height: 10px; }
  .card--back .wordmark__text { font-size: 24px; }
  .card--back .wordmark__text small { display: block; font-size: 12px; letter-spacing: 0.04em; }

  .contact {
    position: absolute; left: 232px; top: 124px;
    list-style: none;
  }
  .contact__item {
    display: flex; align-items: center; gap: 10px;
    height: 30px;
    color: var(--ink-soft); font-weight: 200; font-size: 20px;
  }
  .contact__icon {
    width: 24px; height: 24px;
    border-radius: 4px;
    background: #1a2a36;
    box-shadow: 0 0 8px var(--accent-glow);
    display: flex; align-items: center; justify-content: center;
  }
  .contact__icon svg { width: 16px; height: 16px; fill: none; stroke: var(--ink); stroke-width: 1.6; }
</style>
</head>
<body>
<main class="canvas">

  <section class="card card--front" aria-label="Card front">
    <div class="card__pattern" role="img" aria-label="Dark tonal floral damask pattern"></div>
    <div class="wordmark">
      <span class="wordmark__dot"></span>
      <p class="wordmark__text">ember4<small>business works</small></p>
    </div>
  </section>

  <section class="card card--back" aria-label="Card back">
    <div class="card__pattern" role="img" aria-label="Dark tonal floral damask pattern"></div>
    <div class="wordmark">
      <span class="wordmark__dot"></span>
      <p class="wordmark__text">ember4<small>business works</small></p>
    </div>
    <ul class="contact">
      <li class="contact__item">
        <span class="contact__icon"><svg viewBox="0 0 16 16"><circle cx="8" cy="5.5" r="3"/><path d="M2.5 15c0-3 2.5-5 5.5-5s5.5 2 5.5 5"/></svg></span>
        kai moren
      </li>
      <li class="contact__item">
        <span class="contact__icon"><svg viewBox="0 0 16 16"><circle cx="8" cy="8" r="6.5"/><path d="M1.5 8h13M8 1.5c-3 3.5-3 9.5 0 13M8 1.5c3 3.5 3 9.5 0 13"/></svg></span>
        ember-4.com
      </li>
      <li class="contact__item">
        <span class="contact__icon"><svg viewBox="0 0 16 16"><rect x="1.5" y="3.5" width="13" height="9" rx="1"/><path d="M1.5 4l6.5 5 6.5-5"/></svg></span>
        info@ember-4.com
      </li>
      <li class="contact__item">
        <span class="contact__icon"><svg viewBox="0 0 16 16"><path d="M3 2h3l1.3 3.2-1.8 1.2a8 8 0 0 0 4.1 4.1l1.2-1.8L14 10v3a1.5 1.5 0 0 1-1.5 1.5A11 11 0 0 1 1.5 3.5 1.5 1.5 0 0 1 3 2z"/></svg></span>
        +34 611 204 597
      </li>
    </ul>
  </section>

</main>
</body>
</html>
```